Gestaltung Mini Katalog für bayerische Polomarke
Gestaltung "Mini" Katalog für bayerische Polomarke
Zielgruppe
Unsere Marke richtet sich an den klassischen Lifestyle Kunden. 20 - 45 Jahre alt, legt Wert auf das Äussere und Kleidung.... Mag es gerne besonders, modern und chic.
Hallo,
wir planen derzeit einen kleinen Katalog von 8-10 Seiten im Format DIN A5 (kein Muss). Präsentiert wird darin die erste bayerische Polomarke K&M reitmode und die aktuellen Kollektionen an Polo-Teamshirts.
Die Fotos dazu werden in den nächsten 14 Tagen entstehen.
Wir suchen nun jemanden, der uns das ganze in eine moderne Gestaltung bringt. Für Vorschläge bitte statt der Fotos alternative Fotos einsetzen.
Unsere Marke bewegt sich im mittleren Preissegment und präsentiert eine ganz besondere Sportart. All das muss in dem Katalog rüber kommen. Neben den Produkt- und Modefotos werden klassische Polobilder integriert, um das Gefühl diesen Sports mit zu vermitteln.
Die Grundfarben sollten sich an denen von K&M reitmode orientieren: schwarz, blau, weiss.... Wobei wir für andere Farben, wenn diese passen bzw. begründet sind auch interessiert sind.

```html
<!DOCTYPE html>
<html lang="de">
<head>
<meta charset="utf-8">
<title>Über Uns – K&amp;M reitmode</title>
<link href="https://fonts.googleapis.com/css2?family=Tinos:wght@400;700&display=swap" rel="stylesheet">
<style>
  :root {
    --panel-black: #0b0b0b;
    --text-white: #ffffff;
    --sky-light: #dfe6e4;
    --tree-green: #6f7d4a;
    --field-green: #8fae3c;
    --field-deep: #6e9230;
  }
  html, body {
    margin: 0;
    padding: 0;
    width: 1200px;
    height: 1200px;
    overflow: hidden;
    background: #ffffff;
  }
  .catalog-page {
    position: relative;
    width: 1200px;
    height: 1200px;
    display: flex;
  }
  .about-panel {
    width: 600px;
    height: 1200px;
    background: var(--panel-black);
    color: var(--text-white);
    box-sizing: border-box;
    padding: 72px 30px 0 30px;
    font-family: "Tinos", "Times New Roman", serif;
  }
  .about-title {
    margin: 0 0 38px 0;
    font-size: 32px;
    font-weight: 700;
    line-height: 1.2;
  }
  .about-text {
    margin: 0 0 38px 0;
    font-size: 25.5px;
    line-height: 38px;
    text-align: justify;
    hyphens: auto;
  }
  .polo-photo {
    width: 600px;
    height: 1200px;
    background: linear-gradient(180deg,
      var(--sky-light) 0%,
      var(--tree-green) 4%,
      var(--field-green) 10%,
      var(--field-green) 25%,
      #7fa234 28%,
      var(--field-deep) 34%,
      var(--field-green) 40%,
      #95b344 100%);
  }
</style>
</head>
<body>
  <main class="catalog-page">
    <section class="about-panel">
      <h1 class="about-title">Über Uns</h1>
      <p class="about-text">Die junge Münchner Marke entstand 2008 genau dort, wo der Polosport lebt: direkt am Spielfeldrand, besser gesagt im Isartal Polo Club, den K&amp;M seitdem offiziell ausstattet.</p>
      <p class="about-text">Gegründet wurde das Label von Lena Hofer, Tochter von Georg Hofer, passionierter Polo­spieler, Manager des Isartal Polo Clubs und Leiter der Poloschule Isartal. Besonderes Merkmal jedes Kollektionsstücks: der edle K&amp;M Polospieler. Graf Albrecht nennt sie seine große Leidenschaft, die Prominenz verfolgt das Treiben regelmäßig von der Zuschauertribüne aus und angeblich war auch Konrad Wallner ganz verrückt nach der attraktiven Sportart, die mit viel Eleganz, Pferdestärken und spannenden Zweikämpfen besticht.</p>
      <p class="about-text">"Es ist die Kombination von Reiterei und Teamsport, die Menschen damals wie heute gleichermaßen fasziniert", so Lena Hofer, Gründerin von K&amp;M reitmode. "Infiziert von dieser Leidenschaft habe ich die erste bayerische Polomarke gegründet. Die Kollektion ist dabei eine gelungene Mischung aus klassischer Eleganz und modernen Sportele­menten". K&amp;M reitmode steht für Tradition, urbanen Luxus und sportiven Chic.</p>
    </section>
    <div class="polo-photo" role="img" aria-label="Foto: Polospieler im blauen Trikot reitet auf braunem Pferd über ein grünes Polofeld, im Hintergrund Bäume und Felder"></div>
  </main>
</body>
</html>
```